Business Card for Multi-Brand Sportswear Company

We are looking for a business card which represents our company and the multiple brands within it.

The company: Fen Athletics (LTD)
The brands: Fen, TavaPuni, ElmStretch, Grit and Rain

Employees using these cards would be representing Fen Athletics, rather than any of the individual brands. You will see a current design within the uploaded files, to give some inspiration. The actual text of the brands is not necessary, but the logos should be on there is some format.

Our creative minds on this are stretched, so we are looking for someone to make this their own, and show us what a good business card should look like.

We may like to get these printed with spot gloss, so keep that in mind with your designs.

www.fenathletics.co.uk

Industry/Entity Type

Business

Contact Information for Business Card

Leo Pemberton-Hale
Operations Manager
(+44) 1632 960 418
Leo@fenathletics.co.uk
www.fenathletics.co.uk

Font styles to use
Sans Serif
Other font styles liked:
• Eurostile

Colors
ffffff

Requirements
Nice to have
• Dark (black) background

```html
<!DOCTYPE html>
<html lang="en">
<head>
<meta charset="utf-8">
<title>Fen Athletics – Business Card</title>
<link rel="stylesheet" href="https://fonts.googleapis.com/css2?family=Quicksand:wght@400;500;700&display=swap">
<style>
  :root {
    --backdrop: #8c8c8c;
    --card: #1f1f1f;
    --red: #e02328;
    --white: #ffffff;
    --ink: #1f1f1f;
    --violet: #8a7a96;
    --grey: #a3a3a3;
  }
  * { margin: 0; padding: 0; box-sizing: border-box; }
  html, body { width: 1200px; height: 854px; overflow: hidden; }
  body {
    background: var(--backdrop);
    font-family: "Quicksand", "Helvetica Neue", Arial, sans-serif;
    position: relative;
  }
  .card {
    position: absolute;
    top: 278px;
    width: 598px;
    height: 342px;
    background: var(--card);
    color: var(--white);
    overflow: hidden;
    transform: scale(0.856);
    transform-origin: 0 0;
    box-shadow: 0 6px 16px rgba(0,0,0,.35);
  }
  .card--front { left: 70px; }
  .card--back { left: 601px; }
  .speed-band { position: absolute; left: 0; width: 598px; }
  .card--front .speed-band { top: 47px; height: 49px; }
  .card--back .speed-band { top: 231px; height: 51px; }
  .wordmark { position: absolute; text-align: right; font-weight: 700; line-height: 1; }
  .wordmark__name { display: block; letter-spacing: .5px; }
  .wordmark__tag { display: block; font-weight: 500; letter-spacing: 2px; }
  .card--front .wordmark { right: 98px; top: 56px; color: var(--ink); }
  .card--front .wordmark__name { font-size: 24px; }
  .card--front .wordmark__tag { font-size: 6px; margin-top: 3px; letter-spacing: 1px; }
  .card--back .wordmark { right: 30px; top: 130px; color: var(--white); }
  .card--back .wordmark__name { font-size: 46px; }
  .card--back .wordmark__tag { font-size: 12px; margin-top: 6px; letter-spacing: 2.4px; }
  .brand-row { position: absolute; display: flex; align-items: center; font-weight: 700; white-space: nowrap; }
  .card--front .brand-row { left: 42px; top: 121px; gap: 22px; font-size: 13px; }
  .card--back .brand-row { left: 226px; top: 302px; gap: 14px; font-size: 11px; }
  .brand--elmstretch { color: var(--violet); }
  .brand--grit { color: var(--red); }
  .brand--fen { color: var(--white); }
  .brand--tavapuni { color: var(--grey); }
  .contact { position: absolute; left: 47px; top: 222px; font-size: 16px; line-height: 28px; font-weight: 500; }
  .person { position: absolute; right: 52px; top: 213px; text-align: right; }
  .person__name { font-size: 24px; font-weight: 700; line-height: 32px; }
  .person__role { font-size: 20px; font-weight: 400; margin-top: 6px; }
</style>
</head>
<body>
  <section class="card card--front">
    <svg class="speed-band" viewBox="0 0 598 49" aria-hidden="true">
      <polygon fill="var(--red)" points="0,0 23,0 -26,49 0,49"/>
      <polygon fill="var(--red)" points="35,0 55,0 6,49 -14,49"/>
      <polygon fill="var(--red)" points="70,0 90,0 41,49 21,49"/>
      <polygon fill="var(--red)" points="105,0 125,0 76,49 56,49"/>
      <polygon fill="var(--red)" points="140,0 160,0 111,49 91,49"/>
      <polygon fill="var(--red)" points="188,0 550,0 500,49 140,49"/>
    </svg>
    <div class="wordmark">
      <span class="wordmark__name">Fen Athletics</span>
      <span class="wordmark__tag">PERFORMANCE WEAR</span>
    </div>
    <div class="brand-row">
      <span class="brand--elmstretch">ElmStretch</span>
      <span class="brand--grit">Grit and Rain</span>
      <span class="brand--fen">Fen</span>
      <span class="brand--tavapuni">TavaPuni</span>
    </div>
    <div class="contact">
      <p>(+44) 1632 960 418</p>
      <p>Leo@fenathletics.co.uk</p>
      <p>www.fenathletics.co.uk</p>
    </div>
    <div class="person">
      <p class="person__name">Leo Pemberton-Hale</p>
      <p class="person__role">Operations Manager</p>
    </div>
  </section>

  <section class="card card--back">
    <div class="wordmark">
      <span class="wordmark__name">Fen Athletics</span>
      <span class="wordmark__tag">PERFORMANCE WEAR</span>
    </div>
    <svg class="speed-band" viewBox="0 0 598 51" aria-hidden="true">
      <polygon fill="var(--red)" points="0,0 30,0 -21,51 0,51"/>
      <polygon fill="var(--red)" points="50,0 70,0 19,51 -1,51"/>
      <polygon fill="var(--red)" points="88,0 110,0 59,51 37,51"/>
      <polygon fill="var(--red)" points="128,0 154,0 103,51 77,51"/>
      <polygon fill="var(--red)" points="203,0 569,0 520,51 158,51"/>
    </svg>
    <div class="brand-row">
      <span class="brand--elmstretch">ElmStretch</span>
      <span class="brand--grit">Grit and Rain</span>
      <span class="brand--fen">Fen</span>
      <span class="brand--tavapuni">TavaPuni</span>
    </div>
  </section>
</body>
</html>
```